New Business Card for Web Design/Internet Marketing Company

Looking for a great looking new business card. We are a 10 year old web design, internet marketing and website management company that works mostly with small businesses.

Our new card needs to better match the colors and style of our website, be bold, extremely usable and slightly edgy.

Target Market(s)

Small/Medium businesses that have websites

Industry/Entity Type

Internet

Requirements
Must have
• Front and back design, full color, rounded corners please

Must use the colors/style of our website (JPG provided)

INFO FOR CARDS (as readable as possible please)
Mark Lenner
President/CEO
mark@trelvanmedia.example
Phone: 520-381-7459
Toll Free: 866-381-7459
Address: 4315 W. Calloway Ave. Ste. 140, Tucson, AZ 85792

THINGS I WANT TO PROMOTE (if there is room):
1. Our Website - www.trelvanmedia.example

2. Social Media
Twitter: @trelvanmedia
Facebook: www.facebook.com/trelvanmedia

3. Our Services
Web Design
Internet Marketing
Website Management

```html
<!DOCTYPE html>
<html lang="en">
<head>
<meta charset="utf-8">
<title>Trelvan Media — Business Card, Front and Back</title>
<link rel="stylesheet" href="https://fonts.googleapis.com/css2?family=Open+Sans:wght@400;600;700&display=swap">
<style>
  :root {
    --page: #ece9e4;
    --orange: #f4862e;
    --blue: #1b8bc6;
    --white: #ffffff;
    --ink: #555555;
    --card-shadow: rgba(0, 0, 0, 0.22);
  }
  * { box-sizing: border-box; margin: 0; padding: 0; }
  html, body {
    width: 1200px; height: 758px; overflow: hidden;
    background: var(--page);
    font-family: "Open Sans", Arial, sans-serif;
  }
  .sheet {
    width: 1200px; height: 758px;
    display: flex; align-items: center; justify-content: center; gap: 48px;
  }
  .card {
    position: relative;
    width: 540px; height: 310px;
    border-radius: 22px;
    overflow: hidden;
    box-shadow: 0 10px 26px var(--card-shadow);
  }

  /* Front */
  .card--front { background: var(--orange); }
  .front__top {
    position: absolute; left: 0; top: 0; width: 100%; height: 168px;
    background: var(--white);
    border-bottom: 2px solid var(--blue);
  }
  .brand {
    position: absolute; left: 0; right: 0; top: 46px;
    display: flex; align-items: center; justify-content: center; gap: 12px;
  }
  .brand__dot {
    width: 34px; height: 34px; border-radius: 50%; background: var(--orange);
  }
  .brand__name {
    font-size: 40px; font-weight: 700; color: var(--blue); letter-spacing: -0.5px;
  }
  .name-plate {
    position: absolute; left: 150px; top: 146px; width: 300px; height: 50px;
    background: var(--white);
    display: flex; align-items: center; justify-content: center; gap: 6px;
    color: var(--ink);
  }
  .name-plate__name { font-size: 21px; font-weight: 700; }
  .name-plate__title { font-size: 16px; font-weight: 400; }
  .details {
    position: absolute; left: 24px; right: 24px; top: 214px;
    display: flex; align-items: center; justify-content: center; gap: 14px;
    color: var(--white); font-size: 13px; line-height: 1.5;
  }
  .details__address { text-align: right; }
  .details__rule { width: 1px; align-self: stretch; background: rgba(255,255,255,0.8); }
  .contact { list-style: none; }
  .contact li { display: flex; align-items: center; gap: 6px; }
  .contact svg { width: 11px; height: 11px; flex: none; }

  /* Back */
  .card--back {
    background: var(--orange); color: var(--white);
    display: flex; flex-direction: column; align-items: center; justify-content: center;
    text-align: center;
  }
  .back__brand { display: flex; align-items: center; gap: 14px; margin-bottom: 22px; }
  .back__brand .brand__dot { width: 42px; height: 42px; background: var(--white); }
  .back__brand-name { font-size: 50px; font-weight: 700; letter-spacing: -1px; }
  .services__title { font-size: 24px; font-weight: 700; margin-bottom: 2px; }
  .services__list { font-size: 19px; line-height: 1.3; }
  .social {
    display: flex; gap: 26px; margin-top: 14px; font-size: 13px;
  }
  .social span { display: flex; align-items: center; gap: 6px; }
  .social__mark { width: 12px; height: 12px; background: var(--white); border-radius: 2px; opacity: 0.9; }
</style>
</head>
<body>
<main class="sheet">

  <section class="card card--front" aria-label="Card front">
    <div class="front__top">
      <div class="brand">
        <span class="brand__dot"></span>
        <span class="brand__name">Trelvan Media</span>
      </div>
    </div>
    <div class="name-plate">
      <span class="name-plate__name">Mark Lenner,</span>
      <span class="name-plate__title">President/CEO</span>
    </div>
    <div class="details">
      <address class="details__address" style="font-style:normal">
        4315 W. Calloway Ave. Ste. 140<br>Tucson, AZ 85792
      </address>
      <span class="details__rule"></span>
      <ul class="contact">
        <li><svg viewBox="0 0 12 12"><circle cx="6" cy="6" r="5.5" fill="none" stroke="#fff"/><path d="M4 3.5 5 3 5.6 4.6 5 5.2Q5.6 6.6 6.8 7L7.4 6.4 9 7 8.5 8Q6 8.4 4 5Z" fill="#fff"/></svg>866-381-7459</li>
        <li><svg viewBox="0 0 12 12"><circle cx="6" cy="6" r="5.5" fill="none" stroke="#fff"/><path d="M4 3.5 5 3 5.6 4.6 5 5.2Q5.6 6.6 6.8 7L7.4 6.4 9 7 8.5 8Q6 8.4 4 5Z" fill="#fff"/></svg>520-381-7459</li>
        <li><svg viewBox="0 0 12 12"><circle cx="6" cy="6" r="6" fill="#fff"/><rect x="3" y="4" width="6" height="4.2" fill="none" stroke="#f4862e" stroke-width="0.9"/><path d="M3 4 6 6.4 9 4" fill="none" stroke="#f4862e" stroke-width="0.9"/></svg>mark@trelvanmedia.example</li>
        <li><svg viewBox="0 0 12 12"><circle cx="6" cy="6" r="6" fill="#fff"/><path d="M1 6H11M6 1Q3 6 6 11M6 1Q9 6 6 11" fill="none" stroke="#f4862e" stroke-width="0.8"/></svg>www.trelvanmedia.example</li>
      </ul>
    </div>
  </section>

  <section class="card card--back" aria-label="Card back">
    <div class="back__brand">
      <span class="brand__dot"></span>
      <span class="back__brand-name">Trelvan Media</span>
    </div>
    <h2 class="services__title">Our Services</h2>
    <p class="services__list">• Web Design • Internet Marketing<br>• Website Management</p>
    <div class="social">
      <span><i class="social__mark"></i>@trelvanmedia</span>
      <span><i class="social__mark"></i>trelvanmedia</span>
    </div>
  </section>

</main>
</body>
</html>
```